Roofing Contractor business card redesign

I want to redesign my business card with a fresh, eye catching concept

Target Market(s)

Residential Roofing Clients, potential employees, and subcontractors.

Industry/Entity Type

Business

Colors

Designer to choose colors to be used in the design.

Requirements
Nice to have
• I just want something that's more pleasing to the eye. You can use a combination of either / or of my logos.

```html
<!DOCTYPE html>
<html lang="en">
<head>
<meta charset="utf-8">
<title>Sound Ridge General Contractors – Business Card</title>
<link rel="stylesheet" href="https://fonts.googleapis.com/css2?family=Oswald:wght@500;600&family=Work+Sans:wght@300;400;600&display=swap">
<style>
  :root {
    --page-bg: #ebe5dc;
    --card-orange: #f08a2c;
    --card-orange-light: #f6a85a;
    --brand-brown: #5a2a1c;
    --text-light: #fff4e6;
    --emblem-dark: #4a2418;
    --emblem-orange: #f39a2e;
    --emblem-yellow: #f6c040;
  }
  * { margin: 0; padding: 0; box-sizing: border-box; }
  html, body {
    width: 1200px; height: 1047px; overflow: hidden;
    background: var(--page-bg);
    font-family: "Work Sans", sans-serif;
  }
  .card {
    position: absolute; left: 60px; top: 229px;
    width: 1080px; height: 589px;
    border-radius: 22px;
    background: linear-gradient(90deg, var(--card-orange) 0%, var(--card-orange) 45%, var(--card-orange-light) 100%);
    box-shadow: 0 10px 30px rgba(0,0,0,0.15);
    overflow: hidden;
  }
  .brand {
    position: absolute; left: 49px; top: 70px;
    color: var(--brand-brown);
  }
  .brand-name {
    display: flex; align-items: center; gap: 14px;
    font-weight: 600; font-size: 54px; line-height: 1;
  }
  .brand-dot {
    width: 46px; height: 46px; border-radius: 50%;
    background: var(--brand-brown);
  }
  .brand-sub {
    margin-top: 14px; font-weight: 600; font-size: 29px;
  }
  .contact { position: absolute; left: 49px; top: 240px; color: var(--text-light); }
  .person-name {
    font-family: "Oswald", sans-serif; font-weight: 500;
    font-size: 42px; letter-spacing: 2px; line-height: 1.1;
  }
  .person-title { font-weight: 300; font-size: 24px; line-height: 1.3; letter-spacing: 0.5px; margin-top: 6px; }
  .address { font-weight: 300; font-size: 24px; line-height: 1.35; margin-top: 28px; letter-spacing: 0.5px; }
  .lines { list-style: none; margin-top: 26px; font-weight: 300; font-size: 24px; letter-spacing: 0.5px; }
  .lines li { display: flex; align-items: center; gap: 16px; line-height: 1.4; }
  .lines svg { width: 18px; height: 18px; fill: var(--text-light); flex: none; }
  .emblem {
    position: absolute; left: 528px; top: 5px; width: 527px; height: 400px;
    border-radius: 50% 50% 0 0;
    background: radial-gradient(circle at 50% 55%, var(--emblem-yellow) 0%, var(--emblem-orange) 45%, var(--emblem-dark) 100%);
  }
  .emblem-plate {
    position: absolute; left: 528px; top: 400px; width: 527px; height: 170px;
    background: var(--emblem-dark);
    border: 6px solid var(--emblem-orange);
    border-radius: 10px;
    display: flex; flex-direction: column; align-items: center; justify-content: center;
    color: var(--emblem-orange); font-weight: 600;
  }
  .emblem-plate .plate-name { font-size: 62px; line-height: 1; }
  .emblem-plate .plate-sub { font-size: 28px; margin-top: 10px; }
</style>
</head>
<body>
  <div class="card">
    <div class="brand">
      <div class="brand-name">Sound <span class="brand-dot"></span> Ridge</div>
      <div class="brand-sub">General Contractors, Inc.</div>
    </div>

    <div class="contact">
      <div class="person-name">DALE MORROW</div>
      <div class="person-title">Keller Certified Roof Inspector<br>Licensed Property Adjuster</div>
      <div class="address">4180 Cedar Hollow Road<br>Suite 110 Dallas, TX 75240</div>
      <ul class="lines">
        <li><svg viewBox="0 0 24 24"><path d="M6.6 10.8a15 15 0 0 0 6.6 6.6l2.2-2.2a1 1 0 0 1 1-.25 11.4 11.4 0 0 0 3.6.57 1 1 0 0 1 1 1V20a1 1 0 0 1-1 1A17 17 0 0 1 3 4a1 1 0 0 1 1-1h3.5a1 1 0 0 1 1 1c0 1.25.2 2.45.57 3.6a1 1 0 0 1-.25 1z"/></svg>(972) 555-0148</li>
        <li><svg viewBox="0 0 24 24"><path d="M7 1h10a2 2 0 0 1 2 2v18a2 2 0 0 1-2 2H7a2 2 0 0 1-2-2V3a2 2 0 0 1 2-2zm0 3v14h10V4zm5 15.5a1.2 1.2 0 1 0 0 2.4 1.2 1.2 0 0 0 0-2.4z"/></svg>(972) 555-0193</li>
        <li><svg viewBox="0 0 24 24"><path d="M2 5h20v14H2zm2 2v.5l8 5 8-5V7zm0 2.8V17h16V9.8l-8 5z"/></svg>dale@soundridgetx.com</li>
      </ul>
    </div>

    <div class="emblem" role="img" aria-label="Illustration of a roofer holding a hammer standing behind a house roofline inside a circular badge"></div>
    <div class="emblem-plate">
      <div class="plate-name">Sound Ridge</div>
      <div class="plate-sub">General Contractors, Inc.</div>
    </div>
  </div>
</body>
</html>
```